Easy Marinade Labels for Butchery Store

Need a set of labels designed for a Butchery Shop. They will sit in the top left corner of the packets as a triangle (7cm each side). Easy because the only major requirement is the label name and some small text saying "Please ask in store to see spec sheet for ingredients". Extra points for finding a fun way to incorporate the logo and/or images of food (garlic bulbs, chilli, spices ect) to enhance the label. List of Marinade Names below: GarlicPepper Mint & RosemarySatayBBQChilli Plum & GingerSundried Tomato & BasilBuffaloHoney SoyHoi-SinPer PeriSpicy CajunTeriyakiBlack Bean Ive also attached the logo and an example of how the label might sit on a packet of meat. Thanks

Target Market(s)

Butchery Deli Shop Customers

Industry/Entity Type

Food Store

Font styles to use
Serif
Sans Serif
Decorative
Other font styles liked:
• Fun font that isn't a generic Quellbrix Font?

Colors

Designer to choose colors to be used in the design.

Requirements
Must have
• Product Name
• Small text saying "Please ask in store to see spec sheet for ingredients"
Nice to have
• Photos of ingredients that would match that type of marinade - Chilli, Garlic, Spices.
• Fenly Oak Logo - not essential if it doesn't look good on the label / doesn't fit.

```html
<!DOCTYPE html>
<html lang="en">
<head>
<meta charset="UTF-8">
<title>Honey Soy Marinade Label</title>
<link rel="stylesheet" href="https://fonts.googleapis.com/css2?family=Caveat+Brush&family=Barlow+Semi+Condensed:wght@700&display=swap">
<style>
  :root {
    --page: #ffffff;
    --frame-yellow: #f2f21a;
    --honey-amber: #d9761f;
    --honey-deep: #a33d12;
    --honey-dark: #3d1206;
    --herb-green: #5faa2a;
    --herb-dark: #2f5a1c;
    --label-text: #ffffff;
  }
  * { margin: 0; padding: 0; box-sizing: border-box; }
  html, body {
    width: 1200px;
    height: 900px;
    overflow: hidden;
    background: var(--page);
  }
  .canvas {
    position: relative;
    width: 1200px;
    height: 900px;
    background: var(--page);
  }
  .label-shape {
    position: absolute;
    left: 0;
    top: 0;
  }
  .product-name {
    position: absolute;
    left: 520px;
    top: 370px;
    width: 220px;
    text-align: center;
    font-family: "Caveat Brush", cursive;
    font-size: 78px;
    line-height: 0.98;
    color: var(--label-text);
    letter-spacing: 1px;
    text-shadow: 0 0 2px rgba(0,0,0,0.6);
    transform: rotate(-3deg);
  }
  .product-name .line { display: block; }
  .product-name .line-second { margin-left: -24px; }
  .spec-note {
    position: absolute;
    left: 0;
    width: 1240px;
    top: 598px;
    text-align: center;
    font-family: "Barlow Semi Condensed", sans-serif;
    font-weight: 700;
    font-size: 22px;
    letter-spacing: 2.2px;
    color: var(--label-text);
  }
</style>
</head>
<body>
<main class="canvas">
  <svg class="label-shape" width="1200" height="900" viewBox="0 0 1200 900">
    <defs>
      <linearGradient id="ingredient-tones" x1="0" y1="0" x2="1" y2="0">
        <stop offset="0" stop-color="var(--herb-green)"/>
        <stop offset="0.18" stop-color="var(--honey-amber)"/>
        <stop offset="0.45" stop-color="var(--honey-deep)"/>
        <stop offset="0.62" stop-color="var(--honey-deep)"/>
        <stop offset="0.72" stop-color="var(--herb-green)"/>
        <stop offset="1" stop-color="var(--herb-dark)"/>
      </linearGradient>
      <linearGradient id="base-shade" x1="0" y1="0" x2="0" y2="1">
        <stop offset="0" stop-color="var(--honey-dark)" stop-opacity="0"/>
        <stop offset="1" stop-color="var(--honey-dark)" stop-opacity="0.85"/>
      </linearGradient>
    </defs>
    <polygon class="ingredient-photo" role="img"
      aria-label="Photo of honeycomb with dripping honey and fresh green herb leaves"
      points="620,178 1088,642 152,642" fill="url(#ingredient-tones)"/>
    <polygon class="base-shade" points="540,580 1028,580 1088,642 152,642 214,580"
      fill="url(#base-shade)"/>
    <polygon class="label-frame" points="620,176 1090,643 150,643"
      fill="none" stroke="var(--frame-yellow)" stroke-width="7" stroke-linejoin="miter"/>
  </svg>

  <h1 class="product-name">
    <span class="line">HONEY</span>
    <span class="line line-second">SOY</span>
  </h1>

  <p class="spec-note">PLEASE ASK IN STORE TO SEE SPEC SHEET FOR INGREDIENTS</p>
</main>
</body>
</html>
```